Norrell Advisory WA Business Card

Create an interesting, eye catching and colourful two sided business card. We are a business consulting operation assisting SME's improve all areas of their business. We provide consulting services to assist SME's to create a culture of continuous improvement, making a positive difference in the business. Our tag line is Small changes, big rewards. We want to create a well recognised, innovative brand that can be continued throughout our website, social media and email correspondence.

Target Market(s)

Small to Medium Enterprise Business Owners

Industry/Entity Type

Business Consultant

Contact Information for Business Card

Name of Business: Norrell Advisory - Steady Steps Lasting Gains
Derek Holloway Ph 0407385510 Megan Holloway Ph 0407913847
Email norrelladvisorywa@mailbox-example.com
Web address TBA
FaceBook page TBA

BACKSIDE OF CARD

Providing assistance with:

• Organisation & Efficiency
• Revenue generation & Marketing
• Financial Management
• Production quality & delivery
• Systems & Process documentation
• Exit Strategy

Font styles to use
Other font styles liked:
• Calibri

Colors

Designer to choose colors to be used in the design.

Requirements
Must have
• Calibri font

```html
<!DOCTYPE html>
<html lang="en">
<head>
<meta charset="utf-8">
<title>Norrell Advisory WA Business Card</title>
<link rel="stylesheet" href="https://fonts.googleapis.com/css2?family=Open+Sans:wght@400;600;700&display=swap">
<style>
  :root {
    --page: #e4e4e4;
    --card-light: #ffffff;
    --card-dark: #2f2e2e;
    --brand-blue: #1a7ab8;
    --ink: #333333;
    --ink-soft: #555555;
    --white: #ffffff;
    --green: #7cb342;
    --yellow: #fbc02d;
    --blue: #2a8fc9;
    --red: #e8473a;
  }
  * { margin: 0; padding: 0; box-sizing: border-box; }
  html, body {
    width: 1125px; height: 1200px; overflow: hidden;
    background: var(--page);
    font-family: "Open Sans", Calibri, sans-serif;
  }
  .card {
    position: absolute; left: 157px; width: 825px; height: 472px; overflow: hidden;
  }
  .card--front { top: 106px; background: var(--card-light); }
  .card--back { top: 639px; background: var(--card-dark); }

  .hero-art {
    position: absolute; left: 0; top: 0; width: 320px; height: 279px;
    background: linear-gradient(135deg, var(--blue) 0%, var(--yellow) 35%, var(--green) 60%, var(--red) 100%);
    opacity: .85;
    clip-path: polygon(0 0, 100% 0, 100% 70%, 75% 100%, 0 100%);
  }

  .person { position: absolute; left: 447px; white-space: nowrap; }
  .person__name {
    font-size: 31px; font-weight: 600; color: var(--brand-blue);
    line-height: 1; letter-spacing: .3px; text-transform: uppercase;
  }
  .person__phone {
    margin-top: 6px; font-size: 18px; font-weight: 700; color: var(--ink-soft); line-height: 1;
  }
  .person--first { top: 62px; }
  .person--second { top: 152px; }

  .colour-rule {
    position: absolute; left: 447px; top: 244px; width: 338px; height: 3px; display: flex; gap: 2px;
  }
  .colour-rule span { flex: 1; }
  .colour-rule .c1 { background: var(--green); }
  .colour-rule .c2 { background: var(--yellow); }
  .colour-rule .c3 { background: var(--blue); }
  .colour-rule .c4 { background: var(--red); }

  .contacts { position: absolute; left: 447px; top: 286px; width: 370px; list-style: none; }
  .contacts li {
    display: flex; align-items: center; height: 31px; margin-bottom: 10px;
    font-size: 15.5px; color: var(--ink-soft); white-space: nowrap;
  }
  .contacts svg { width: 31px; height: 31px; margin-right: 12px; flex: none; }

  .brand { position: absolute; text-align: center; white-space: nowrap; }
  .brand__name { font-weight: 700; line-height: 1; text-transform: uppercase; }
  .brand__tagline { text-transform: uppercase; line-height: 1; }
  .brand--front { left: 16px; top: 338px; width: 362px; }
  .brand--front .brand__name { font-size: 30px; color: var(--ink); }
  .brand--front .brand__tagline { margin-top: 8px; font-size: 15px; letter-spacing: 1.8px; color: var(--ink-soft); }
  .brand--back { left: 62px; top: 276px; width: 310px; }
  .brand--back .brand__name { font-size: 26px; color: var(--white); }
  .brand--back .brand__tagline { margin-top: 6px; font-size: 13px; letter-spacing: 1.5px; color: var(--white); }

  .services { position: absolute; left: 402px; top: 128px; }
  .services__title { font-size: 27px; font-weight: 700; color: var(--brand-blue); line-height: 1.2; white-space: nowrap; }
  .services__list { list-style: none; margin-top: 13px; }
  .services__list li {
    position: absolute; left: 20px; font-size: 18px; color: var(--white); line-height: 1;
    white-space: nowrap;
  }
  .services__list li::before {
    content: ""; position: absolute; left: -19px; top: 4px; width: 11px; height: 11px;
    background: var(--blue);
  }
  .services__list li:nth-child(1) { top: 51px; }
  .services__list li:nth-child(2) { top: 77px; }
  .services__list li:nth-child(3) { top: 103px; }
  .services__list li:nth-child(4) { top: 130px; }
  .services__list li:nth-child(5) { top: 156px; }
  .services__list li:nth-child(6) { top: 182px; }
</style>
</head>
<body>
  <section class="card card--front">
    <div class="hero-art" role="img" aria-label="Cluster of colourful interlocking jigsaw pieces in blue, yellow, green and red"></div>

    <div class="person person--first">
      <p class="person__name">Derek Holloway</p>
      <p class="person__phone">0407385510</p>
    </div>
    <div class="person person--second">
      <p class="person__name">Megan Holloway</p>
      <p class="person__phone">0407913847</p>
    </div>

    <div class="colour-rule"><span class="c1"></span><span class="c2"></span><span class="c3"></span><span class="c4"></span></div>

    <ul class="contacts">
      <li>
        <svg viewBox="0 0 31 31" aria-hidden="true"><circle cx="15.5" cy="15.5" r="15.5" fill="var(--brand-blue)"/><rect x="8.5" y="10.5" width="14" height="10" fill="none" stroke="#fff" stroke-width="1.6"/><path d="M8.5 10.5 L15.5 16 L22.5 10.5" fill="none" stroke="#fff" stroke-width="1.6"/></svg>
        norrelladvisorywa@mailbox-example.com
      </li>
      <li>
        <svg viewBox="0 0 31 31" aria-hidden="true"><circle cx="15.5" cy="15.5" r="15.5" fill="var(--brand-blue)"/><circle cx="15.5" cy="15.5" r="7.5" fill="none" stroke="#fff" stroke-width="1.6"/><ellipse cx="15.5" cy="15.5" rx="3.2" ry="7.5" fill="none" stroke="#fff" stroke-width="1.4"/><line x1="8" y1="15.5" x2="23" y2="15.5" stroke="#fff" stroke-width="1.4"/></svg>
        www.norrelladvisorywa-example.com
      </li>
      <li>
        <svg viewBox="0 0 31 31" aria-hidden="true"><circle cx="15.5" cy="15.5" r="15.5" fill="var(--brand-blue)"/></svg>
        norrelladvisory.wa
      </li>
    </ul>

    <div class="brand brand--front">
      <p class="brand__name">Norrell Advisory</p>
      <p class="brand__tagline">Steady Steps Lasting Gains</p>
    </div>
  </section>

  <section class="card card--back">
    <div class="brand brand--back">
      <p class="brand__name">Norrell Advisory</p>
      <p class="brand__tagline">Steady Steps Lasting Gains</p>
    </div>

    <div class="services">
      <h2 class="services__title">Providing assistance with</h2>
      <ul class="services__list">
        <li>Organisation &amp; Efficiency</li>
        <li>Revenue generation &amp; Marketing</li>
        <li>Financial Management</li>
        <li>Production quality &amp; delivery</li>
        <li>Systems &amp; Process documentation</li>
        <li>Exit Strategy</li>
      </ul>
    </div>
  </section>
</body>
</html>
```